Young, dynamic furniture company needs a new business card design

We require a new business card design for our modern furniture company which supplies furniture and appliances to the property and development market.
Oakridge Interiors has become one of the leading furniture & appliance suppliers to the property market withing London. With over 10 years experience, we have increased our business to supply not only private landlords and managing agents, but also property developers, housing associations and local councils.
We offer not only a complete range of furniture which includes beds, wardrobes, dining sets and sofas, but also a high quality, full delivery and assembly service to help you with all our furnishing needs.

Target Market(s)

Private landlords, estate agents, letting agents, property management companies

Industry/Entity Type

Business

Contact Information for Business Card

Name,
Title,
Address,
Mobile,
Telephone,
Fax, Website, email address

Font styles to use
Sans Serif

Colors
3176b5
0555a3
85abd2
cfdeed

Requirements
Must have
• All the above information for each of our staff, along with our logo

```html
<!DOCTYPE html>
<html lang="en">
<head>
<meta charset="utf-8">
<title>Oakridge Interiors – Business Card</title>
<link href="https://fonts.googleapis.com/css2?family=Arimo:wght@400;700&display=swap" rel="stylesheet">
<style>
  :root {
    --backdrop: #3b3c3f;
    --navy: #1f4a92;
    --brand-blue: #0555a3;
    --accent-blue: #3176b5;
    --sky: #85abd2;
    --charcoal: #232325;
    --white: #ffffff;
    --ink: #2a2a2c;
  }
  * { box-sizing: border-box; margin: 0; padding: 0; }
  html, body {
    width: 1200px; height: 950px; overflow: hidden;
    background: var(--backdrop);
    font-family: "Arimo", Arial, sans-serif;
  }
  .canvas { position: relative; width: 1200px; height: 950px; }
  .card {
    position: absolute; width: 620px; height: 354px;
    overflow: hidden; border-radius: 3px;
    box-shadow: 0 14px 30px rgba(0,0,0,.35);
  }

  /* Back of card */
  .card-back {
    left: 70px; top: 110px;
    background: var(--navy);
    color: var(--white);
    display: flex; flex-direction: column; align-items: center; justify-content: center;
    text-align: center;
  }
  .brand { display: flex; align-items: center; gap: 12px; white-space: nowrap; }
  .brand-square { width: 22px; height: 22px; background: currentColor; flex: none; }
  .brand-name { font-weight: 700; font-size: 30px; letter-spacing: 1px; text-transform: uppercase; }
  .brand-tagline { font-size: 11px; letter-spacing: 1.5px; text-transform: uppercase; margin-top: 6px; white-space: nowrap; }
  .card-back .brand-tagline { margin-left: 34px; }
  .back-copy { font-size: 15px; line-height: 1.45; margin-top: 34px; }

  /* Front of card */
  .card-front { left: 510px; top: 486px; background: var(--charcoal); }
  .front-shapes { position: absolute; inset: 0; }
  .front-brand {
    position: absolute; left: 312px; top: 84px; color: var(--ink);
  }
  .front-brand .brand { gap: 10px; }
  .front-brand .brand-name { font-size: 22px; letter-spacing: .5px; }
  .front-brand .brand-square { width: 17px; height: 17px; background: var(--brand-blue); }
  .front-brand .brand-tagline { font-size: 9.5px; margin-left: 27px; color: var(--ink); }

  .contact { position: absolute; left: 40px; top: 116px; color: var(--white); }
  .person-name { font-weight: 700; font-size: 19px; line-height: 22px; letter-spacing: .5px; text-transform: uppercase; }
  .person-title { font-size: 14px; line-height: 17px; text-transform: uppercase; margin-top: 3px; }
  .address { font-size: 13.5px; line-height: 19px; margin-top: 18px; }
  .contact-list { list-style: none; margin-top: 10px; }
  .contact-list li { display: flex; align-items: center; gap: 9px; font-size: 13.5px; line-height: 19px; height: 19px; }
  .contact-list svg { width: 12px; height: 12px; flex: none; fill: var(--white); }
</style>
</head>
<body>
<main class="canvas">

  <section class="card card-back">
    <div class="brand">
      <span class="brand-square"></span>
      <span class="brand-name">Oakridge Interiors</span>
    </div>
    <p class="brand-tagline">Trade Furniture Solutions</p>
    <p class="back-copy">High quality, full delivery &amp; assembly<br>service to help you with all our furnishing needs.</p>
  </section>

  <section class="card card-front">
    <svg class="front-shapes" viewBox="0 0 620 354" aria-hidden="true">
      <polygon points="230,0 620,0 620,250 283,210 256,184" fill="var(--brand-blue)"/>
      <polygon points="620,244 290,206 286,210 620,250" fill="var(--sky)"/>
      <polygon points="245,0 620,0 620,236 292,198 270,176" fill="var(--white)"/>
    </svg>

    <div class="front-brand">
      <div class="brand">
        <span class="brand-square"></span>
        <span class="brand-name">Oakridge Interiors</span>
      </div>
      <p class="brand-tagline">Trade Furniture Solutions</p>
    </div>

    <div class="contact">
      <p class="person-name">Daniel Marsh</p>
      <p class="person-title">President</p>
      <p class="address">2715 Harlow Avenue<br>Greenfield, NY 11420</p>
      <ul class="contact-list">
        <li>
          <svg viewBox="0 0 12 12"><path d="M1 4c0-2 2-3 5-3s5 1 5 3l-2 1-1-2H4L3 5zM2 6h8l1 5H1z"/></svg>
          574 2196 4408
        </li>
        <li>
          <svg viewBox="0 0 12 12"><path d="M3 0h6a1 1 0 0 1 1 1v10a1 1 0 0 1-1 1H3a1 1 0 0 1-1-1V1a1 1 0 0 1 1-1zm0 2v7h6V2z"/></svg>
          861 5037 2914
        </li>
        <li>
          <svg viewBox="0 0 12 12"><path d="M3 0h6v3H3zM1 4h10v5H9v3H3V9H1zm3 4v3h4V8z"/></svg>
          853 7740 1629
        </li>
        <li>
          <svg viewBox="0 0 12 12"><path d="M0 2h12v8H0zm1 1v.5l5 3.5 5-3.5V3z"/></svg>
          daniel@oakridgemail.com
        </li>
        <li>
          <svg viewBox="0 0 12 12"><circle cx="6" cy="6" r="5.5"/></svg>
          www.oakridgeinteriors.com
        </li>
      </ul>
    </div>
  </section>

</main>
</body>
</html>
```